Business Cards for new orthopaedic surgery practice

My husband and I are starting our own orthopaedic surgery practice. We are looking for a business card that is uniform, but one will have my name/title and the other will have his. You can just create one design with my name on it for now. But when I choose your design as the winning design I will ask that you add another copy with his name/title.

We are looking for classy, simple, elite all in one. We like dark blues/a little gold/yellow. Something that goes with our logo. We want our logo incorporated. Here is all the info you need:
Business name: RV Bone & Vitality Center
Location: 38517 North Willowmere Ave
Seabreeze Hills, FL 33990
Phone: 954-218-4063
Fax: 954-582-7341
Email: info@myrvbonecare.example

Names: Lydia Vance, M.D.
Board Certified Hand and Upper Extremity Surgeon

Ebo Dansu, M.D.
Board Certified Hip & Knee Replacement/General Orthopaedic Surgeon

Can decide what you want to put on the back. Maybe a slogan:
Rooted in Care. Focused on You

I am just going to upload our logo. The only thing is if we select you as the winning design, the location, and phone numbers may change. We will need your help to update that once fully solidified.

Industry/Entity Type

Medical

Contact Information for Business Card

Colors
0054AA
0677BA
7BADD7
CADEEF
E8F1F8
0094D4
00A9DD
6FCCEA
C7EBF8
E9F6FB

Requirements
Must have
• class, appeal,
Should not have
• We want to air on the side of masculine if we are looking at masculine vs. feminine feel. But we still want it classy, sophisticated, and something we will love

```html
<!DOCTYPE html>
<html lang="en">
<head>
<meta charset="utf-8">
<title>RV Bone &amp; Vitality Center — Business Card</title>
<link rel="stylesheet" href="https://fonts.googleapis.com/css2?family=Montserrat:wght@500;600&display=swap">
<style>
  :root {
    --navy: #1c2a52;
    --gold: #c49a58;
    --paper: #ffffff;
    --ink: #1e1e24;
    --backdrop: #3b3b3d;
  }
  * { margin: 0; padding: 0; box-sizing: border-box; }
  html, body { width: 1200px; height: 1200px; overflow: hidden; }
  body {
    background: var(--backdrop);
    font-family: "Montserrat", Arial, sans-serif;
    position: relative;
  }
  .card {
    position: absolute;
    left: 100px;
    width: 1000px;
    height: 560px;
    border-radius: 42px;
    overflow: hidden;
  }
  .card--front { top: 30px; background: var(--paper); }
  .card--back { top: 610px; background: var(--navy); }

  .front-band { position: absolute; inset: 0; width: 100%; height: 100%; }

  .doctor { position: absolute; left: 80px; top: 165px; }
  .doctor__name {
    color: var(--gold);
    font-weight: 600;
    font-size: 36px;
    letter-spacing: 0.5px;
  }
  .doctor__title {
    color: var(--ink);
    font-weight: 500;
    font-size: 23px;
    line-height: 1.15;
    margin-top: 6px;
  }

  .contact { position: absolute; left: 80px; top: 330px; list-style: none; }
  .contact__item {
    display: flex;
    align-items: center;
    gap: 16px;
    color: var(--ink);
    font-weight: 500;
    font-size: 26px;
    height: 42px;
  }
  .contact__icon { width: 28px; height: 28px; fill: var(--gold); flex: none; }

  .brand {
    position: absolute;
    display: flex;
    align-items: center;
    justify-content: center;
    border-radius: 50%;
    border: 3px solid var(--gold);
    text-align: center;
    font-weight: 600;
    text-transform: uppercase;
  }
  .brand--front {
    left: 620px; top: 50px; width: 300px; height: 300px;
    color: var(--navy); font-size: 25px; letter-spacing: 3px; line-height: 1.5;
  }
  .brand--back {
    left: 320px; top: 100px; width: 360px; height: 360px;
    color: var(--paper); font-size: 30px; letter-spacing: 4px; line-height: 1.5;
  }

  .address {
    position: absolute;
    left: 665px; top: 458px;
    display: flex; align-items: center; gap: 12px;
    color: var(--paper);
    font-weight: 500;
    font-style: normal;
    font-size: 18px;
    line-height: 1.3;
  }
  .address__pin { width: 22px; height: 30px; fill: var(--gold); flex: none; }
</style>
</head>
<body>

<section class="card card--front">
  <svg class="front-band" viewBox="0 0 1000 560" preserveAspectRatio="none" aria-hidden="true">
    <path d="M0,512 L560,512 C600,512 612,470 628,440" fill="none" stroke="var(--gold)" stroke-width="12"/>
    <path d="M0,524 L560,524 C612,524 622,428 700,428 L1000,428 L1000,560 L0,560 Z" fill="var(--navy)"/>
  </svg>

  <div class="doctor">
    <h1 class="doctor__name">LYDIA VANCE, M.D.</h1>
    <p class="doctor__title">Board Certified Hand and<br>Upper Extremity Surgeon</p>
  </div>

  <ul class="contact">
    <li class="contact__item">
      <svg class="contact__icon" viewBox="0 0 24 24" aria-hidden="true"><path d="M6.6 10.8a15.1 15.1 0 0 0 6.6 6.6l2.2-2.2a1 1 0 0 1 1-.25 11.4 11.4 0 0 0 3.6.57 1 1 0 0 1 1 1V20a1 1 0 0 1-1 1A17 17 0 0 1 3 4a1 1 0 0 1 1-1h3.5a1 1 0 0 1 1 1c0 1.250.2 2.450.57 3.570a1 1 0 0 1-.25 1z"/></svg>
      <span>954-218-4063</span>
    </li>
    <li class="contact__item">
      <svg class="contact__icon" viewBox="0 0 24 24" aria-hidden="true"><path d="M6 2h9l3 3v5H6zM3 11h18a1 1 0 0 1 1 1v9a1 1 0 0 1-1 1H3a1 1 0 0 1-1-1v-9a1 1 0 0 1 1-1zm3 3v2h2v-2zm4 0v2h2v-2zm4 0v2h4v-2zm-8 4v2h2v-2zm4 0v2h2v-2z"/></svg>
      <span>954-582-7341</span>
    </li>
    <li class="contact__item">
      <svg class="contact__icon" viewBox="0 0 24 24" aria-hidden="true"><path d="M2 5h20v14H2zm2 2v.5l8 5.5 8-5.5V7zm0 3v7h16v-7l-8 5.5z"/></svg>
      <span>info@myrvbonecare.example</span>
    </li>
  </ul>

  <div class="brand brand--front">RV Bone &amp;<br>Vitality<br>Center</div>

  <address class="address">
    <svg class="address__pin" viewBox="0 0 22 30" aria-hidden="true"><path d="M11 0a11 11 0 0 0-11 11c0 8 11 19 11 19s11-11 11-19A11 11 0 0 0 11 0zm0 15a4 4 0 1 1 0-8 4 4 0 0 1 0 8z"/></svg>
    <span>38517 North Willowmere Ave<br>Seabreeze Hills, FL 33990</span>
  </address>
</section>

<section class="card card--back">
  <div class="brand brand--back">RV Bone &amp;<br>Vitality<br>Center</div>
</section>

</body>
</html>
```